Create a business promotion flyer to leave in customer mailboxes. We are a bulk petroleum supplier, servicing any industry that requires diesel. Base in griffith NSW, servicing griffith area and surrounds.

Business Name - Terra Diesel
Fuel@terradiesel-example.com.au
Owen - 0491 570 362 ohartley@terradiesel-example.com.au
Liam - 0491 570 718 lprosser@terradiesel-example.com.au
Simon - 0491 570 905 skenway@terradiesel-example.com.au
Office 02 5550 1734

Bulk Fuel deliveries.
Oils & lubricants
Local Family owned business

```html
<!DOCTYPE html>
<html lang="en">
<head>
<meta charset="utf-8">
<title>Terra Diesel – Bulk Petroleum Supplier Flyer</title>
<link rel="stylesheet" href="https://fonts.googleapis.com/css2?family=Fjalla+One&family=Oswald:wght@500;600&family=Poppins:wght@500;600&family=Montserrat:wght@700&display=swap">
<style>
  :root{
    --backdrop:#919191;
    --red:#ee2a1d;
    --grey:#666666;
    --ink:#2b2b2b;
    --white:#ffffff;
    --blush:#fcecea;
    --sky-top:#3f78c4;
    --sky-low:#bcd3ec;
    --ground:#cfcac4;
  }
  *{margin:0;padding:0;box-sizing:border-box}
  html,body{width:964px;height:1200px;overflow:hidden;background:var(--backdrop)}
  .flyer{position:absolute;left:172px;top:134px;width:620px;height:931px;background:var(--blush);overflow:hidden}
  .flyer-shapes{position:absolute;inset:0;width:620px;height:931px}
  .brand-name{position:absolute;left:340px;top:44px;width:260px;text-align:center;font-family:'Poppins',sans-serif;font-weight:600;font-size:34px;color:var(--red);letter-spacing:.5px}
  .headline{position:absolute;left:26px;top:24px;font-family:'Fjalla One',sans-serif;font-weight:400;font-size:59px;line-height:62px;color:var(--white)}
  .subhead{position:absolute;left:26px;top:286px;font-family:'Fjalla One',sans-serif;font-size:27px;line-height:34px;color:var(--white)}
  .services-title{position:absolute;left:26px;top:474px;font-family:'Oswald',sans-serif;font-weight:600;font-size:36px;line-height:44px;color:var(--red)}
  .service{position:absolute;left:26px;display:flex;align-items:center;gap:17px}
  .service-icon{flex:none;width:65px;height:59px;display:flex;align-items:center;justify-content:center}
  .service-icon.grey{background:var(--grey)}
  .service-icon.red{background:var(--red)}
  .service-label{font-family:'Oswald',sans-serif;font-weight:500;font-size:23px;line-height:27px;color:var(--ink)}
  .contact-title{position:absolute;right:24px;top:660px;font-family:'Oswald',sans-serif;font-weight:600;font-size:25px;color:var(--white)}
  .contact{position:absolute;left:370px;top:706px;width:272px;text-align:center;color:var(--white);font-style:normal}
  .contact-email{font-family:'Poppins',sans-serif;font-weight:500;font-size:9px;margin-top:3px}
  .contact-phone-icon{margin-top:8px}
  .contact-name{font-family:'Poppins',sans-serif;font-weight:500;font-size:12.5px;line-height:14px}
  .contact-number{font-family:'Montserrat',sans-serif;font-weight:700;font-size:27px;line-height:31px;margin-bottom:3px}
</style>
</head>
<body>
<main class="flyer">
  <svg class="flyer-shapes" viewBox="0 0 1115 1673" preserveAspectRatio="none">
    <defs>
      <linearGradient id="photoTones" x1="0" y1="0" x2="0" y2="1">
        <stop offset="0" stop-color="var(--sky-top)"/>
        <stop offset="0.3" stop-color="var(--sky-low)"/>
        <stop offset="0.5" stop-color="#e8eaec"/>
        <stop offset="0.62" stop-color="#9a9a9a"/>
        <stop offset="0.66" stop-color="var(--ground)"/>
        <stop offset="1" stop-color="#dad6d0"/>
      </linearGradient>
    </defs>
    <path class="logo-panel" d="M470 0 H1115 V195 Q1085 210 1040 210 H660 Q600 210 568 158 Z" fill="var(--white)"/>
    <path class="hero-panel" d="M0 0 H450 L560 190 Q600 265 568 340 L400 700 Q368 765 290 765 H0 Z" fill="var(--red)"/>
    <path class="services-panel" d="M0 790 H300 Q380 790 410 845 L620 1200 Q640 1250 620 1300 L440 1673 H0 Z" fill="var(--white)"/>
    <path class="photo-frame" d="M770 275 H1115 V1148 H720 Q650 1148 612 1080 L452 770 Q425 710 460 645 L620 355 Q665 275 770 275 Z" fill="var(--red)"/>
    <g role="img" aria-label="Photo of a white fuel tanker truck parked in front of a depot shed under a blue sky">
      <path d="M800 275 H1115 V1140 H770 Q705 1140 670 1075 L512 770 Q488 715 518 655 L676 348 Q712 275 800 275 Z" fill="url(#photoTones)"/>
    </g>
    <path class="contact-tab" d="M715 1250 Q745 1178 810 1178 H1115 V1250 Z" fill="var(--grey)"/>
    <path class="contact-panel" d="M478 1673 L705 1290 Q728 1250 780 1250 H1115 V1673 Z" fill="var(--red)"/>
  </svg>

  <div class="brand-name">Terra Diesel</div>

  <h1 class="headline">We Are<br>A Bulk<br>Petroleum<br>Supplier</h1>
  <p class="subhead">Servicing any<br>industry that<br>requires diesel</p>

  <h2 class="services-title">SERVICES</h2>

  <div class="service" style="top:531px">
    <div class="service-icon grey">
      <svg width="42" height="26" viewBox="0 0 42 26" fill="var(--white)"><rect x="1" y="3" width="24" height="13" rx="6"/><path d="M27 6h7l5 6v6H27z"/><circle cx="8" cy="21" r="3.5"/><circle cx="17" cy="21" r="3.5"/><circle cx="33" cy="21" r="3.5"/></svg>
    </div>
    <div class="service-label">Bulk Fuel<br>Deliveries</div>
  </div>

  <div class="service" style="top:611px">
    <div class="service-icon red">
      <svg width="30" height="34" viewBox="0 0 30 34" fill="var(--white)"><path d="M6 8h12l6 8v15H4V12z"/><rect x="9" y="2" width="7" height="5" rx="1"/><circle cx="20" cy="25" r="6" fill="var(--red)"/><path d="M20 20c2 3 3 4 3 5.5a3 3 0 0 1-6 0c0-1.5 1-2.5 3-5.5z"/></svg>
    </div>
    <div class="service-label">Oils &amp; Lubricants</div>
  </div>

  <div class="service" style="top:691px">
    <div class="service-icon grey">
      <svg width="42" height="28" viewBox="0 0 42 28" fill="none" stroke="var(--white)" stroke-width="2.5"><rect x="2" y="3" width="10" height="11"/><rect x="13" y="3" width="10" height="11"/><path d="M2 17h24V8h6l6 7v6H2z"/><circle cx="9" cy="23" r="3"/><circle cx="32" cy="23" r="3"/></svg>
    </div>
    <div class="service-label">Petrol Deliveries</div>
  </div>

  <div class="service" style="top:770px">
    <div class="service-icon red">
      <svg width="36" height="36" viewBox="0 0 36 36" fill="var(--white)"><path d="M18 2l7 3v6c0 4-3 7-7 8-4-1-7-4-7-8V5z"/><path d="M14.5 10l2.5 2.5 4.5-4.5" stroke="var(--red)" stroke-width="2" fill="none"/><circle cx="8" cy="23" r="3.5"/><circle cx="28" cy="23" r="3.5"/><circle cx="18" cy="24" r="4"/><path d="M2 34c0-5 3-7 6-7s6 2 6 7zM22 34c0-5 3-7 6-7s6 2 6 7zM11 35c0-5 3-7 7-7s7 2 7 7z"/></svg>
    </div>
    <div class="service-label">Local Family<br>Owned Business</div>
  </div>

  <h2 class="contact-title">CONTACT US</h2>

  <address class="contact">
    <svg width="14" height="10" viewBox="0 0 14 10"><rect x="0.5" y="0.5" width="13" height="9" fill="var(--white)"/><path d="M1 1l6 5 6-5" stroke="var(--red)" fill="none"/></svg>
    <div class="contact-email">Fuel@terradiesel-example.com.au</div>
    <svg class="contact-phone-icon" width="14" height="14" viewBox="0 0 24 24" fill="var(--white)"><path d="M6.6 10.8a15 15 0 0 0 6.6 6.6l2.2-2.2a1 1 0 0 1 1-.25 11 11 0 0 0 3.6.6 1 1 0 0 1 1 1V20a1 1 0 0 1-1 1A17 17 0 0 1 3 4a1 1 0 0 1 1-1h3.5a1 1 0 0 1 1 1c0 1.25.2 2.45.6 3.6a1 1 0 0 1-.25 1z"/></svg>
    <div class="contact-name">Owen</div>
    <div class="contact-number">0491 570 362</div>
    <div class="contact-name">Liam</div>
    <div class="contact-number">0491 570 718</div>
    <div class="contact-name">Simon</div>
    <div class="contact-number">0491 570 905</div>
  </address>
</main>
</body>
</html>
```